Walk Beside The River

Business Card design

Target Market(s)

People who require support in the commnity

Industry/Entity Type

Mental Health Support

Contact Information for Business Card

Mental Health Support Rosalind Tavener walkbesidetheriver@mailcove.com.au 0481 637 092 PO Box 926 Tallowbrook VIC 3871

Colors
6B429C
8869AF
B7A5CE
E3DAEB
F3F0F8

Requirements
Must have
• Logo & details listed above
Should not have
• No red or orange

```html
<!DOCTYPE html>
<html lang="en">
<head>
<meta charset="utf-8">
<title>Walk Beside The River – Business Card</title>
<link rel="stylesheet" href="https://fonts.googleapis.com/css2?family=Open+Sans:wght@400;600;700&display=swap">
<style>
  :root {
    --stage: #2b2b2f;
    --card: #1f1e23;
    --card-deep: #18171b;
    --yellow: #f0e62c;
    --purple: #6b429c;
    --purple-mid: #8869af;
    --white: #ffffff;
    --silver: #4a4a52;
  }
  * { box-sizing: border-box; margin: 0; padding: 0; }
  html, body {
    width: 1200px; height: 780px; overflow: hidden;
    background: var(--stage);
    font-family: "Open Sans", Arial, sans-serif;
  }
  .canvas { position: relative; width: 1200px; height: 780px; }

  .card {
    position: absolute;
    top: 236px;
    width: 540px; height: 309px;
    border-radius: 18px;
    border: 3px solid var(--yellow);
    overflow: hidden;
    background: var(--card);
  }
  .card--front { left: 40px; }
  .card--back { left: 620px; background: var(--card-deep); }

  /* Front */
  .brand {
    position: absolute; left: 150px; top: 26px;
    display: flex; align-items: center; gap: 12px;
  }
  .brand__dot { width: 54px; height: 54px; border-radius: 50%; background: var(--purple); }
  .brand__name { color: var(--white); font-weight: 600; font-size: 15px; letter-spacing: 0.3px; }

  .person { position: absolute; left: 22px; top: 100px; }
  .person__marker {
    position: absolute; left: 0; top: 2px;
    width: 7px; height: 32px; background: var(--yellow);
  }
  .person__name {
    margin-left: 16px;
    font-weight: 700; font-size: 29px; line-height: 36px;
    color: var(--yellow);
  }
  .person__surname { color: var(--purple-mid); }
  .person__role {
    margin-left: 2px; margin-top: 2px;
    color: var(--white); font-size: 14px;
  }

  .contacts {
    position: absolute; left: 22px; top: 170px;
    list-style: none; color: var(--white); font-size: 13px; line-height: 22px;
  }
  .contacts li { display: flex; align-items: center; gap: 8px; }
  .contacts svg { width: 12px; height: 12px; flex: none; }

  .service {
    position: absolute; left: 318px; top: 198px;
    color: var(--white); font-size: 15px; line-height: 21px;
  }

  .edge-bands { position: absolute; left: 0; bottom: 0; width: 540px; height: 44px; }

  /* Back */
  .pattern {
    position: absolute; inset: 0;
    background: linear-gradient(100deg, var(--card-deep) 0%, var(--card) 55%, var(--silver) 100%);
  }
  .back-brand {
    position: absolute; inset: 0;
    display: flex; align-items: center; justify-content: center; gap: 14px;
  }
  .back-brand__dot { width: 46px; height: 46px; border-radius: 50%; background: var(--yellow); }
  .back-brand__name { color: var(--yellow); font-weight: 600; font-size: 22px; }
</style>
</head>
<body>
<main class="canvas">

  <section class="card card--front" aria-label="Business card front">
    <div class="brand">
      <span class="brand__dot"></span>
      <span class="brand__name">Walk Beside The River</span>
    </div>

    <div class="person">
      <span class="person__marker"></span>
      <h1 class="person__name">Helena <span class="person__surname">Marvasi</span></h1>
      <p class="person__role">CEO/Director</p>
    </div>

    <ul class="contacts">
      <li>
        <svg viewBox="0 0 12 12"><path d="M3 1l2 2.5-1.2 1.2a7 7 0 0 0 3.5 3.5L8.5 7 11 9l-1.5 2C5 11 1 7 1 2.5z" fill="var(--yellow)"/></svg>
        0481 637 092
      </li>
      <li>
        <svg viewBox="0 0 12 12"><rect x="1" y="2.5" width="10" height="7" rx="1" fill="none" stroke="var(--yellow)" stroke-width="1.3"/><path d="M1.5 3l4.5 3.5L10.5 3" fill="none" stroke="var(--yellow)" stroke-width="1.3"/></svg>
        walkbesidetheriver@mailcove.com.au
      </li>
      <li>
        <svg viewBox="0 0 12 12"><path d="M6 11S2 7 2 4.5a4 4 0 0 1 8 0C10 7 6 11 6 11z" fill="var(--yellow)"/><circle cx="6" cy="4.5" r="1.5" fill="var(--card)"/></svg>
        PO Box 926 Tallowbrook VIC 3871
      </li>
    </ul>

    <p class="service">Mental Health Support<br>Rosalind Tavener</p>

    <svg class="edge-bands" viewBox="0 0 540 44" aria-hidden="true">
      <line x1="0" y1="16" x2="258" y2="16" stroke="var(--yellow)" stroke-width="2"/>
      <polygon points="0,20 258,20 266,44 0,44" fill="var(--purple)"/>
      <polygon points="254,8 540,8 540,44 268,44" fill="var(--yellow)"/>
    </svg>
  </section>

  <section class="card card--back" aria-label="Business card back">
    <div class="pattern" role="img" aria-label="Repeating small star pattern on black, glinting silver toward the right"></div>
    <div class="back-brand">
      <span class="back-brand__dot"></span>
      <span class="back-brand__name">Walk Beside The River</span>
    </div>
  </section>

</main>
</body>
</html>
```